Gala Dinner Flyer for State Water Polo Association

We need a promotional flyer for the "2016 Coral Soiree" - a fundraising gala dinner for Tidewave Sport Collective to distribute to our members.

The details for the event are as follows:

Date: Saturday 16th April 2016
Time: 7pm to Midnight
Venue: Marlowe C, Brindle Wharf, 84 Tamsin Parade, Docklands 3008
Cost: $150 per person
Details: Canapés on arrival followed by a three course dinner, with premium beverages throughout the evening.
RSVP: Friday 8th April 2016
Dress Code: Black Tie
For tickets for to www.tixmondo.com.au/tickets/event/coralsoiree

We also require an event logo with a minimum height of 200px, and event background with a minimum width of 1200px and height of 800px, and flyer image with a minimum width of 620px and height of 874px.

I have attached a number of logos we need incorporated along with last years invitation and a few photos from last years event.

We would like to use designs that use water and the colour blue.

The final design should communicate elegance and high class

Target Market(s)

25-60 year old Men and Women from affluent families

Industry/Entity Type

Promotional

Colors
1861ab
3277b5
85acd3
cedeed
ffffff

Requirements
Must have
• Tidewave Sport Collective Logo, Southern Herons Logo, quietharbor Logo & Kestrel Holdings Logo

```html
<!DOCTYPE html>
<html lang="en">
<head>
<meta charset="utf-8">
<title>2016 Coral Soiree – Gala Dinner Flyer</title>
<link rel="stylesheet" href="https://fonts.googleapis.com/css2?family=Raleway:wght@200;300;400&family=Great+Vibes&family=Roboto+Condensed:wght@400;700&display=swap">
<style>
  :root {
    --ink: #050608;
    --deep: #0c1118;
    --blue: #1861ab;
    --blue-mid: #3277b5;
    --blue-bright: #2a9fe0;
    --blue-soft: #85acd3;
    --blue-pale: #cedeed;
    --white: #ffffff;
    --row-light: #f2f2f2;
    --row-shade: #c9c9c9;
    --row-text: #1b1b1b;
  }
  * { box-sizing: border-box; margin: 0; padding: 0; }
  html, body { width: 849px; height: 1200px; overflow: hidden; background: var(--white); }
  .flyer {
    position: relative;
    width: 849px;
    height: 1200px;
    overflow: hidden;
    background: radial-gradient(ellipse at 50% 30%, #16202c 0%, var(--ink) 65%);
    font-family: "Roboto Condensed", sans-serif;
  }
  .backdrop { position: absolute; inset: 0; }

  .title {
    position: absolute;
    top: 150px; left: 0; width: 849px;
    text-align: center;
    color: var(--blue-bright);
  }
  .title-year {
    font-family: "Raleway", sans-serif;
    font-weight: 200;
    font-size: 64px;
    letter-spacing: 2px;
    line-height: 1;
  }
  .title-main {
    font-family: "Raleway", sans-serif;
    font-weight: 200;
    font-size: 128px;
    letter-spacing: 6px;
    line-height: 1;
    margin-top: 4px;
  }
  .title-script {
    font-family: "Great Vibes", cursive;
    color: var(--white);
    font-size: 118px;
    line-height: 1;
    margin-top: -26px;
    margin-left: 120px;
  }

  .date-ribbon {
    position: absolute;
    top: 553px; left: 0; width: 849px;
    text-align: center;
    font-family: "Raleway", sans-serif;
    font-weight: 400;
    font-size: 36px;
    letter-spacing: 3px;
    color: var(--white);
    line-height: 58px;
  }

  .details {
    position: absolute;
    top: 642px; left: 155px;
    width: 560px;
    list-style: none;
  }
  .detail-row {
    display: flex;
    height: 46px;
    margin-bottom: 10px;
  }
  .detail-label {
    width: 175px;
    padding-left: 38px;
    font-family: "Raleway", sans-serif;
    font-weight: 400;
    font-size: 21px;
    letter-spacing: 1px;
    color: var(--white);
    text-transform: uppercase;
    line-height: 46px;
  }
  .detail-value {
    flex: 1;
    display: flex;
    flex-direction: column;
    justify-content: center;
    align-items: center;
    text-align: center;
    font-weight: 700;
    font-size: 17px;
    color: var(--row-text);
    text-transform: uppercase;
    line-height: 1.15;
  }
  .detail-value small {
    font-weight: 400;
    font-size: 11px;
    text-transform: none;
  }
  .detail-value.is-note {
    font-size: 11.5px;
    font-weight: 700;
    text-transform: none;
    padding: 0 30px;
  }

  .tickets {
    position: absolute;
    top: 995px; left: 0; width: 849px;
    text-align: center;
    font-weight: 700;
    font-size: 19px;
    letter-spacing: 0.5px;
    color: var(--blue-bright);
  }
  .tickets span { color: var(--white); }

  .partners {
    position: absolute;
    top: 1045px; left: 150px;
    width: 560px;
    display: flex;
    justify-content: space-between;
    align-items: center;
  }
  .partner {
    display: flex;
    align-items: center;
    gap: 7px;
    font-weight: 400;
    font-size: 14px;
    color: var(--blue-pale);
    letter-spacing: 0.5px;
  }
  .partner-mark {
    width: 22px; height: 22px;
    border-radius: 50%;
    background: var(--blue-mid);
    flex: none;
  }
</style>
</head>
<body>
<main class="flyer">
  <svg class="backdrop" width="849" height="1200" viewBox="0 0 849 1200" xmlns="http://www.w3.org/2000/svg">
    <defs>
      <radialGradient id="bokeh" cx="50%" cy="50%" r="50%">
        <stop offset="0" stop-color="#2a9fe0" stop-opacity="0.55"/>
        <stop offset="1" stop-color="#1861ab" stop-opacity="0.15"/>
      </radialGradient>
      <linearGradient id="photo-warm" x1="0" y1="0" x2="1" y2="1">
        <stop offset="0" stop-color="#5a5a5a"/>
        <stop offset="1" stop-color="#141414"/>
      </linearGradient>
      <linearGradient id="photo-blue" x1="0" y1="0" x2="1" y2="1">
        <stop offset="0" stop-color="#3b4d63"/>
        <stop offset="1" stop-color="#0d141d"/>
      </linearGradient>
      <radialGradient id="title-disc" cx="50%" cy="50%" r="50%">
        <stop offset="0" stop-color="#141a22"/>
        <stop offset="1" stop-color="#07090c"/>
      </radialGradient>
      <linearGradient id="ribbon" x1="0" y1="0" x2="0" y2="1">
        <stop offset="0" stop-color="#2a9fe0"/>
        <stop offset="1" stop-color="#1861ab"/>
      </linearGradient>
      <linearGradient id="tab" x1="0" y1="0" x2="1" y2="0">
        <stop offset="0" stop-color="#1861ab"/>
        <stop offset="1" stop-color="#2a9fe0"/>
      </linearGradient>
      <linearGradient id="row" x1="0" y1="0" x2="1" y2="0">
        <stop offset="0" stop-color="#c9c9c9"/>
        <stop offset="0.5" stop-color="#f4f4f4"/>
        <stop offset="1" stop-color="#c9c9c9"/>
      </linearGradient>
    </defs>

    <!-- soft blue bokeh -->
    <g class="bokeh-lights" fill="url(#bokeh)">
      <circle cx="760" cy="470" r="42"/>
      <circle cx="812" cy="560" r="24"/>
      <circle cx="70" cy="520" r="34"/>
      <circle cx="40" cy="640" r="18"/>
      <circle cx="800" cy="700" r="30"/>
      <circle cx="110" cy="860" r="22"/>
      <circle cx="770" cy="900" r="16"/>
      <circle cx="640" cy="120" r="20"/>
      <circle cx="200" cy="60" r="14"/>
      <circle cx="560" cy="510" r="26"/>
      <circle cx="290" cy="520" r="18"/>
    </g>

    <!-- event photo circles -->
    <circle cx="150" cy="130" r="150" fill="url(#photo-warm)" role="img" aria-label="Photo of performers on stage at last year's gala"/>
    <circle cx="730" cy="110" r="120" fill="url(#photo-blue)" role="img" aria-label="Photo of the gala dining room set for dinner"/>
    <circle cx="790" cy="300" r="70" fill="url(#photo-blue)" role="img" aria-label="Photo of guests at a table"/>
    <circle cx="60" cy="360" r="78" fill="url(#photo-warm)" role="img" aria-label="Photo of guests dancing"/>
    <circle cx="190" cy="430" r="52" fill="url(#photo-blue)" role="img" aria-label="Photo of the band playing"/>
    <circle cx="670" cy="420" r="48" fill="url(#photo-warm)" role="img" aria-label="Photo of guests raising a toast"/>

    <!-- title disc -->
    <circle cx="424" cy="315" r="248" fill="url(#title-disc)" stroke="#1861ab" stroke-opacity="0.35" stroke-width="2"/>

    <!-- date ribbon -->
    <polygon points="120,568 160,560 160,612 120,620 136,592" fill="#0f4682"/>
    <polygon points="729,560 769,568 753,592 769,620 729,612" fill="#0f4682"/>
    <polygon points="145,550 704,546 729,552 729,606 704,612 145,616" fill="url(#ribbon)"/>

    <!-- detail rows -->
    <g class="detail-shapes">
      <g transform="translate(0,642)"><polygon points="140,0 330,0 330,46 140,46" fill="url(#tab)"/><polygon points="140,46 155,46 155,54" fill="#0f4682"/><rect x="330" y="0" width="385" height="46" fill="url(#row)"/></g>
      <g transform="translate(0,698)"><polygon points="140,0 330,0 330,46 140,46" fill="url(#tab)"/><polygon points="140,46 155,46 155,54" fill="#0f4682"/><rect x="330" y="0" width="385" height="46" fill="url(#row)"/></g>
      <g transform="translate(0,754)"><polygon points="140,0 330,0 330,46 140,46" fill="url(#tab)"/><polygon points="140,46 155,46 155,54" fill="#0f4682"/><rect x="330" y="0" width="385" height="46" fill="url(#row)"/></g>
      <g transform="translate(0,810)"><polygon points="140,0 330,0 330,46 140,46" fill="url(#tab)"/><polygon points="140,46 155,46 155,54" fill="#0f4682"/><rect x="330" y="0" width="385" height="46" fill="url(#row)"/></g>
      <g transform="translate(0,866)"><polygon points="140,0 330,0 330,46 140,46" fill="url(#tab)"/><polygon points="140,46 155,46 155,54" fill="#0f4682"/><rect x="330" y="0" width="385" height="46" fill="url(#row)"/></g>
      <g transform="translate(0,922)"><polygon points="140,0 330,0 330,46 140,46" fill="url(#tab)"/><polygon points="140,46 155,46 155,54" fill="#0f4682"/><rect x="330" y="0" width="385" height="46" fill="url(#row)"/></g>
    </g>
  </svg>

  <h1 class="title">
    <div class="title-year">2016</div>
    <div class="title-main">CORAL</div>
    <div class="title-script">Soiree</div>
  </h1>

  <p class="date-ribbon">SATURDAY 16TH APRIL 2016</p>

  <ul class="details">
    <li class="detail-row"><span class="detail-label">Time</span><span class="detail-value">7.00PM till midnight</span></li>
    <li class="detail-row"><span class="detail-label">Venue</span><span class="detail-value">Marlowe C, Brindle Wharf<small>84 Tamsin Parade, Docklands 3008</small></span></li>
    <li class="detail-row"><span class="detail-label">Details</span><span class="detail-value is-note">Canapés on arrival followed by a three course dinner with premium beverages throughout the evening</span></li>
    <li class="detail-row"><span class="detail-label">Cost</span><span class="detail-value">$150 per person</span></li>
    <li class="detail-row"><span class="detail-label">Dress</span><span class="detail-value">Black tie</span></li>
    <li class="detail-row"><span class="detail-label">RSVP</span><span class="detail-value">Friday 8th April 2016</span></li>
  </ul>

  <p class="tickets">FOR TICKETS <span>GO TO www.tixmondo.com.au/tickets/event/coralsoiree</span></p>

  <div class="partners">
    <div class="partner"><span class="partner-mark"></span>Southern Herons</div>
    <div class="partner"><span class="partner-mark"></span>Tidewave Sport Collective</div>
    <div class="partner"><span class="partner-mark"></span>quietharbor</div>
    <div class="partner">KESTREL HOLDINGS</div>
  </div>
</main>
</body>
</html>
```